Animal Eye Clinic needs a Business card

We are a new veterinary ophthalmology practice (Ridgeline Pet Vision Care) and we need a business card designed. We only see animal eyes - we are not a regular veterinary clinic. We already have a logo. We are looking for a professional, good looking business card to hand out to our clients. We are looking for something simple but professional and contemporary. Our logo is likely the only picture/graphic that needs to be on the card.
Updates

Contact Information for Business Card

Delia Vossman, BSc, DVM, MSc, DipACVO
Veterinary Ophthalmologist

Phone: 250.418.3927
Email: ridgelinepetvisioncare@mailbox-example.net
Website: ridgelinepetvisioncare-example.net
Address: 1874 Thornbury Rd
Kelowna, BC, V1X 4M9

Colors

Designer to choose colors to be used in the design.

Requirements
Must have
• Our logo (attached)

```html
<!DOCTYPE html>
<html lang="en">
<head>
<meta charset="utf-8">
<title>Ridgeline Pet Vision Care – Business Card</title>
<link href="https://fonts.googleapis.com/css2?family=Archivo:wght@700;800&family=Roboto+Condensed:wght@400;700&display=swap" rel="stylesheet">
<style>
  :root {
    --bg: #2a2a2a;
    --card: #151515;
    --teal: #1d9aa8;
    --teal-faint: #15302f;
    --grey: #8d8d8d;
    --light: #a9a9a9;
  }
  * { margin: 0; padding: 0; box-sizing: border-box; }
  html, body {
    width: 1200px; height: 900px; overflow: hidden;
    background: var(--bg);
  }
  .stage {
    width: 1200px; height: 900px;
    display: flex; flex-direction: column; align-items: center; justify-content: center;
    gap: 40px;
  }
  .card {
    width: 700px; height: 400px;
    background: var(--card);
    position: relative; overflow: hidden;
    box-shadow: 0 10px 30px rgba(0,0,0,.45);
  }
  /* Front */
  .card-front .backdrop-circle {
    position: absolute; left: 250px; top: 40px;
    width: 330px; height: 330px; border-radius: 50%;
    background: var(--teal-faint);
  }
  .brand {
    position: absolute; left: 0; right: 0; top: 0; bottom: 0;
    display: flex; align-items: center; justify-content: center;
  }
  .brand-name {
    font-family: "Archivo", sans-serif; font-weight: 800;
    font-size: 38px; color: var(--teal); letter-spacing: .5px;
    text-transform: uppercase; position: relative;
  }
  /* Back */
  .card-back .content {
    position: absolute; left: 48px; right: 30px; top: 135px;
    display: flex; align-items: stretch;
  }
  .person { text-align: right; padding-right: 22px; }
  .person-name {
    font-family: "Archivo", sans-serif; font-weight: 800;
    font-size: 30px; color: var(--teal); line-height: 1.05; letter-spacing: .5px;
  }
  .person-credentials {
    font-family: "Roboto Condensed", sans-serif; font-weight: 700;
    font-size: 19px; color: var(--teal); margin-top: 4px;
  }
  .person-title {
    font-family: "Roboto Condensed", sans-serif; font-weight: 400;
    font-size: 19px; color: var(--grey); margin-top: 2px;
  }
  .divider { width: 2px; background: var(--teal); }
  .contact {
    list-style: none; padding-left: 18px;
    font-family: "Roboto Condensed", sans-serif; font-size: 17px; color: var(--light);
  }
  .contact li { display: flex; align-items: center; gap: 9px; line-height: 27px; white-space: nowrap; }
  .contact svg { width: 20px; height: 20px; flex: none; }
  .contact .address { padding-left: 0; }
</style>
</head>
<body>
<main class="stage">
  <section class="card card-front">
    <div class="backdrop-circle" role="img" aria-label="Faint circular backdrop behind the practice name"></div>
    <div class="brand">
      <span class="brand-name">Ridgeline Pet Vision Care</span>
    </div>
  </section>

  <section class="card card-back">
    <div class="content">
      <div class="person">
        <h1 class="person-name">DELIA VOSSMAN</h1>
        <p class="person-credentials">BSc, DVM, MSc, DipACVO</p>
        <p class="person-title">Veterinary Ophthalmologist</p>
      </div>
      <div class="divider"></div>
      <ul class="contact">
        <li>
          <svg viewBox="0 0 24 24" fill="none" stroke="#1d9aa8" stroke-width="1.6"><circle cx="12" cy="12" r="10"/><path d="M8.5 7.5l2 2-1 1.5c.8 1.6 1.9 2.7 3.5 3.5l1.5-1 2 2-1.3 1.3c-3.5-.4-7.6-4.5-8-8z"/></svg>
          250.418.3927
        </li>
        <li>
          <svg viewBox="0 0 24 24" fill="none" stroke="#1d9aa8" stroke-width="1.6"><rect x="3" y="6" width="18" height="12"/><path d="M3 6l9 7 9-7"/></svg>
          ridgelinepetvisioncare@mailbox-example.net
        </li>
        <li>
          <svg viewBox="0 0 24 24" fill="none" stroke="#1d9aa8" stroke-width="1.6"><circle cx="12" cy="12" r="9"/><path d="M3 12h18M12 3c3 3 3 15 0 18M12 3c-3 3-3 15 0 18"/></svg>
          www.ridgelinepetvisioncare-example.net
        </li>
        <li class="address">1874 Thornbury Rd, Kelowna, BC, V1X 4M9</li>
      </ul>
    </div>
  </section>
</main>
</body>
</html>
```